Brindle Children's Center - Child Care brochure

I just bought a new child care and completely renovated the space. We are also designing a new website, so I need the brochure to match that with updated info. www.brindlechildrenscenter.com - Information on there is current. We expect to have the new one up and running in the next few days. We have new photo's that I'd like to be added to the flyer too. ps. the boys in the pictures are mine, so i would appreciate one of them being added :). support@netcrafterhub.com has details on the website (dev.brindlechildrenscenter.com). The child care program is only open during the ski season - i.e. a resort facility catering to high end clients.
I'm attaching the the website information, the flyer I created, logo files and pictures.

Target Market(s)

Parents of young children

Font styles to use
Other font styles liked:
• "Things we said" & "Calibri Light"

Colors
cfeae6
fef1ee

Requirements
Must have
• Pictures of children. sleek design - winter, mountain theme. Check with website designer on new website.
Nice to have
• prices included
Should not have
• Kid like artwork

```html
<!DOCTYPE html>
<html lang="en">
<head>
<meta charset="utf-8">
<title>Brindle Children's Center – Brochure</title>
<link href="https://fonts.googleapis.com/css2?family=Carlito:wght@400;700&family=Schoolbell&display=swap" rel="stylesheet">
<style>
  :root{
    --stage:#e7e7e7;
    --mint:#cfeae6;
    --mint-deep:#a7d6cf;
    --teal:#7fc2b9;
    --teal-ink:#4e9f96;
    --blush:#fef1ee;
    --rose:#ecdad5;
    --salmon:#e58d80;
    --ink:#5f6b6b;
    --ink-soft:#8a9595;
    --white:#ffffff;
    --photo-warm-a:#b99a82;
    --photo-warm-b:#6f5a4c;
    --photo-blue:#3d4f78;
    --photo-snow:#dfe6ee;
  }
  *{box-sizing:border-box;margin:0;padding:0}
  html,body{width:1200px;height:2400px;overflow:hidden}
  body{background:var(--stage);font-family:"Carlito",sans-serif;color:var(--ink);position:relative}

  .spread{position:absolute;left:45px;width:1110px;height:858px;display:flex;box-shadow:0 12px 30px rgba(0,0,0,.12)}
  .spread--outside{top:262px}
  .spread--inside{top:1280px}
  .panel{position:relative;width:370px;height:858px;overflow:hidden}

  .heading{font-family:"Schoolbell",cursive;color:var(--teal-ink);font-size:27px;line-height:1.1;font-weight:400}
  .heading--sm{font-size:22px}
  .subhead{font-family:"Schoolbell",cursive;color:var(--salmon);font-size:18px;margin-top:8px}
  .copy{font-size:13.5px;line-height:1.4;color:var(--ink)}
  .copy + .copy{margin-top:6px}

  .photo{position:absolute;display:block}
  .photo--round{border-radius:50%;border:5px solid var(--white);box-shadow:0 0 0 2px var(--mint-deep)}

  .brand{display:flex;align-items:center;justify-content:center;gap:8px;font-family:"Schoolbell",cursive;color:var(--teal-ink);font-size:24px;white-space:nowrap}
  .brand__dot{width:16px;height:16px;border-radius:50%;background:var(--teal)}

  /* Outside – reservations */
  .panel--reservations{background:var(--white)}
  .panel--reservations .wave{position:absolute;left:0;top:0}
  .panel--reservations .content{position:absolute;left:34px;right:30px;top:58px}
  .form-lines{list-style:none;margin:6px 0 8px}
  .form-lines li{font-size:13px;display:flex;gap:6px;margin-bottom:5px}
  .form-lines li span{flex:1;border-bottom:1px solid var(--ink-soft)}
  .panel--reservations .photo{left:0;top:610px;width:370px;height:180px;background:linear-gradient(135deg,#d9a9b7,#8c6f7d 55%,#c9b3a6)}
  .panel--reservations .foot{position:absolute;left:0;bottom:0;width:100%;height:68px;background:var(--teal)}

  /* Outside – info / rates */
  .panel--info{background:var(--rose)}
  .panel--info .photo{left:0;top:0;width:370px;height:175px;background:linear-gradient(180deg,#8fa9c9,#eef2f6 55%,#7b6a62)}
  .panel--info .brand{position:absolute;top:200px;width:100%;font-size:22px}
  .panel--info .serving{position:absolute;top:248px;width:100%;text-align:center;font-size:14px;line-height:1.3}
  .hours{position:absolute;top:300px;left:48px;right:48px;height:36px;border-radius:18px;background:var(--white);text-align:center;font-family:"Schoolbell",cursive;font-size:21px;line-height:36px;color:var(--teal-ink)}
  .rates{position:absolute;top:360px;left:30px;right:30px}
  .rates .heading{text-align:center;font-size:32px}
  .rates__cols{display:flex;justify-content:space-between;margin-top:6px}
  .rate-list{list-style:none;font-size:13px;line-height:1.45}
  .rate-list__title{color:var(--salmon);font-weight:700;letter-spacing:.5px}
  .panel--info .wave{position:absolute;left:0;bottom:0}
  .contact{position:absolute;left:0;right:0;top:690px;text-align:center;font-size:14px;line-height:1.45;color:var(--white)}
  .contact .web{font-family:"Schoolbell",cursive;font-size:19px;margin-top:14px}

  /* Outside – cover */
  .panel--cover{background:linear-gradient(180deg,var(--white) 0%,var(--white) 60%,var(--mint) 100%)}
  .panel--cover .brand{position:absolute;top:52px;width:100%;font-size:26px}
  .panel--cover .photo--hero{left:0;top:140px;width:370px;height:520px;background:linear-gradient(160deg,var(--white) 0%,var(--photo-warm-a) 25%,var(--photo-blue) 65%,var(--photo-warm-b) 100%)}
  .panel--cover .photo--round{left:196px;top:455px;width:160px;height:160px;background:linear-gradient(135deg,#c6a99a,#6d7f96)}
  .panel--cover .wave{position:absolute;left:0;bottom:0}
  .cover-name{position:absolute;top:720px;width:100%;text-align:center;font-family:"Schoolbell",cursive;font-size:28px;color:var(--white)}
  .cover-web{position:absolute;top:772px;width:100%;text-align:center;font-family:"Schoolbell",cursive;font-size:19px;color:var(--teal-ink)}

  /* Inside – welcome */
  .panel--welcome{background:var(--mint)}
  .panel--welcome .content{position:absolute;left:30px;right:28px;top:40px}
  .services{list-style:none;margin-top:6px}
  .services li{font-size:13.5px;line-height:1.45;display:flex;align-items:center;gap:8px}
  .services li::before{content:"";width:7px;height:7px;background:var(--teal-ink)}
  .panel--welcome .photo{left:0;top:620px;width:370px;height:238px;background:linear-gradient(135deg,#a07a5a,#d8c0a8 45%,#8e9eb0)}
  .panel--welcome .wave{position:absolute;left:0;top:600px}

  /* Inside – program / staff */
  .panel--program,.panel--staff{background:var(--white)}
  .panel--program .photo--top,.panel--staff .photo--top{left:0;top:0;width:370px;height:190px}
  .panel--program .photo--top{background:linear-gradient(135deg,#c8a07f,#e6b1b8 50%,#5f7fa8)}
  .panel--staff .photo--top{background:linear-gradient(135deg,#d6c49a,#b98a7a 50%,#e7e1d4)}
  .panel--program .photo--round{left:236px;top:118px;width:110px;height:110px;background:linear-gradient(135deg,#e6c0a3,#9a7c6a)}
  .panel--staff .photo--round{left:40px;top:110px;width:110px;height:110px;background:linear-gradient(135deg,#8fb5d6,#e2c3a6)}
  .panel .body{position:absolute;left:30px;right:28px;top:240px}
  .bring{list-style:none;margin-top:4px}
  .bring li{font-size:13.5px;line-height:1.4;padding-left:14px;position:relative;margin-bottom:6px}
  .bring li::before{content:"";position:absolute;left:0;top:7px;width:6px;height:6px;border-radius:50%;background:var(--teal)}
  .panel--staff .fade{position:absolute;left:0;bottom:0;width:100%;height:220px;background:linear-gradient(180deg,var(--white),var(--mint))}
  .panel--staff .brand{position:absolute;bottom:70px;width:100%}
</style>
</head>
<body>

<section class="spread spread--outside">
  <article class="panel panel--reservations">
    <svg class="wave" width="370" height="60" viewBox="0 0 370 60"><path d="M0 0H370V22C260 48 120 8 0 34Z" fill="#cfeae6"/></svg>
    <div class="content">
      <h2 class="heading">Reservations</h2>
      <p class="copy">We highly recommend that reservations be made in advance to ensure space for your child. To make a reservation contact us at (555) 014-2287. We have limited capacity.</p>
      <h3 class="heading heading--sm" style="margin-top:12px">Reservation confirmation</h3>
      <ul class="form-lines">
        <li>Confirmation number <span></span></li>
        <li>Child's name <span></span></li>
        <li>Reserved date <span></span></li>
        <li>Reservation time <span></span></li>
      </ul>
      <p class="copy">Your reservation fee will be applied to your full fee of service.</p>
      <h3 class="heading heading--sm" style="margin-top:12px">Cancellation Policy</h3>
      <p class="copy">Reservations must be cancelled 24 hours in advance of the time of service or the full fee will be charged for all days not cancelled.</p>
    </div>
    <div class="photo" role="img" aria-label="Photo of two young girls playing together at a table"></div>
    <div class="foot"></div>
  </article>

  <article class="panel panel--info">
    <div class="photo" role="img" aria-label="Photo of the snowy mountain resort village"></div>
    <div class="brand"><span class="brand__dot"></span>Brindle Children's Center</div>
    <p class="serving">Serving children ages<br>6 wks thru 8 years</p>
    <div class="hours">Open daily: 8:30-4:30</div>
    <div class="rates">
      <h2 class="heading">Rates</h2>
      <div class="rates__cols">
        <ul class="rate-list">
          <li class="rate-list__title">INFANT / TODDLER</li>
          <li>$105/full day</li>
          <li>$65/half day</li>
          <li>$410/four day package</li>
        </ul>
        <ul class="rate-list">
          <li class="rate-list__title">3 YEARS AND UP</li>
          <li>$95/full day</li>
          <li>$60/half day</li>
          <li>$360/four day package</li>
        </ul>
      </div>
    </div>
    <svg class="wave" width="370" height="230" viewBox="0 0 370 230"><path d="M0 40C120 0 250 10 370 50V230H0Z" fill="#a7d6cf"/><path d="M0 62C130 20 250 30 370 70V230H0Z" fill="#7fc2b9"/></svg>
    <div class="contact">
      <p>P.O. Box 4127</p>
      <p>Brindle, Utah 84000</p>
      <p>(555) 014-2287</p>
      <p>info@brindlechildrenscenter.com</p>
      <p class="web">www.brindlechildrenscenter.com</p>
    </div>
  </article>

  <article class="panel panel--cover">
    <div class="brand"><span class="brand__dot"></span>Brindle Children's Center</div>
    <div class="photo photo--hero" role="img" aria-label="Photo of a smiling young boy in a blue sweater inside the classroom"></div>
    <div class="photo photo--round" role="img" aria-label="Round photo of a caregiver with a toddler"></div>
    <svg class="wave" width="370" height="230" viewBox="0 0 370 230"><path d="M0 30C140 70 260 40 370 0V230H0Z" fill="#fef1ee"/><path d="M0 52C140 92 260 62 370 22V230H0Z" fill="#7fc2b9"/></svg>
    <p class="cover-name">Brindle Children's Center</p>
    <p class="cover-web">www.brindlechildrenscenter.com</p>
  </article>
</section>

<section class="spread spread--inside">
  <article class="panel panel--welcome">
    <div class="content">
      <h2 class="heading">Welcome to the<br>Brindle Children's Center</h2>
      <p class="copy" style="margin-top:8px">When you hit the slopes you want to make sure your children are in good hands. At the Brindle Children's Center we offer a warm, safe place where your little ones can play, learn and make new friends while you enjoy the mountain.</p>
      <h3 class="heading heading--sm" style="margin-top:12px">Our Services</h3>
      <p class="copy">The Brindle Children's Center is a full service childcare facility that caters to children from six weeks to eight years old. Infants, toddlers and young children will explore the center with caring, experienced instructors.</p>
      <p class="copy">Children visiting the center can look forward to the following activities:</p>
      <ul class="services">
        <li>Dramatic play</li>
        <li>Arts and Crafts</li>
        <li>Discovery Science</li>
        <li>Snow Play</li>
        <li>Stories</li>
        <li>Music</li>
        <li>Nutritious lunch and snacks</li>
      </ul>
    </div>
    <svg class="wave" width="370" height="40" viewBox="0 0 370 40"><path d="M0 0H370V14C250 40 120 4 0 26Z" fill="#cfeae6"/></svg>
    <div class="photo" role="img" aria-label="Photo of a toddler reading a book beside a large teddy bear" style="top:624px;z-index:-0"></div>
  </article>

  <article class="panel panel--program">
    <div class="photo photo--top" role="img" aria-label="Photo of children playing dress-up in the classroom"></div>
    <div class="photo photo--round" role="img" aria-label="Round photo of a child at play"></div>
    <div class="body">
      <h2 class="heading">Our program</h2>
      <p class="copy">The Brindle Children's Center is fully licensed by the State of Utah and offers a program that caters to your child's needs.</p>
      <h3 class="subhead">Infants</h3>
      <p class="copy">Our infant care program is open to children six weeks to eighteen months. We follow your baby's own routine for feeding, naps and play.</p>
      <h3 class="subhead">Toddlers</h3>
      <p class="copy">Children ages 18 months to three years will enjoy music, stories, snow play and simple crafts in a gentle daily rhythm.</p>
      <h3 class="subhead">Age Three &amp; Up</h3>
      <p class="copy">With new friends, your child will explore science, art and outdoor winter games every day.</p>
      <h3 class="subhead">Evenings</h3>
      <p class="copy">The center offers evening care for families by request. Please ask our staff about availability for your stay.</p>
    </div>
  </article>

  <article class="panel panel--staff">
    <div class="photo photo--top" role="img" aria-label="Photo of a child painting at a craft table"></div>
    <div class="photo photo--round" role="img" aria-label="Round photo of a baby smiling"></div>
    <div class="fade"></div>
    <div class="body">
      <h2 class="heading">Our staff</h2>
      <p class="copy">At the Brindle Children's Center our staff takes pride in creating a nurturing and creative atmosphere where your child can learn and grow. Each member of our team is trained in child development, first aid and CPR.</p>
      <h3 class="heading heading--sm" style="margin-top:14px">Things to bring with you</h3>
      <ul class="bring">
        <li>For infants, parents should supply diapers, wipes, a change of clothes, formula and bottles.</li>
        <li>For toddlers, parents should supply diapers or pull-ups, wipes and a change of clothes.</li>
        <li>For ages 3 and up, parents should supply a change of clothes, snow boots, mittens and a warm hat for outdoor play.</li>
      </ul>
    </div>
    <div class="brand"><span class="brand__dot"></span>Brindle Children's Center</div>
  </article>
</section>

</body>
</html>
```